Global (re)insurance broker needs a business card design

We need a classic business card for our company that is headquartered in SG, with offices in Malaysia and Dubai. We specialise in insurance and reinsurance broking and consultancy for our global clients.

```html
<!DOCTYPE html>
<html lang="en">
<head>
<meta charset="utf-8">
<title>Norvale business card</title>
<link rel="stylesheet" href="https://fonts.googleapis.com/css2?family=Open+Sans:wght@400;600;700&display=swap">
<style>
  :root {
    --backdrop: #333336;
    --card: #1f1e23;
    --brand-blue: #2c4fa6;
    --brand-green: #c5dfba;
    --ink-light: #eceef0;
    --ink-soft: #c9ccd2;
  }
  * { box-sizing: border-box; margin: 0; padding: 0; }
  html, body {
    width: 1200px; height: 780px; overflow: hidden;
    background: var(--backdrop);
    font-family: "Open Sans", Arial, sans-serif;
  }
  .stage {
    width: 1200px; height: 780px;
    display: flex; align-items: center; justify-content: center; gap: 44px;
  }
  .card {
    position: relative;
    width: 534px; height: 305px;
    background: var(--card);
    box-shadow: 0 10px 28px rgba(0,0,0,.35);
    overflow: hidden;
  }
  /* detail side */
  .holder {
    position: absolute; left: 30px; top: 26px;
    padding-left: 12px;
    border-left: 6px solid var(--brand-blue);
  }
  .holder-name {
    font-size: 27px; font-weight: 600; line-height: 1;
    color: var(--brand-blue);
  }
  .holder-name .surname { color: var(--brand-green); font-weight: 700; }
  .holder-role {
    margin-top: 4px;
    font-size: 12px; color: var(--ink-light); letter-spacing: .2px;
  }
  .contact-list {
    position: absolute; left: 30px; bottom: 26px;
    list-style: none;
    font-size: 12.5px; color: var(--ink-light); line-height: 1.55;
  }
  .contact-list li { display: flex; align-items: center; gap: 8px; }
  .contact-list svg { width: 12px; height: 12px; flex: none; }
  .address {
    position: absolute; right: 28px; bottom: 26px;
    text-align: left;
    font-size: 14px; color: var(--ink-light); line-height: 1.45;
  }
  .wordmark {
    font-weight: 700; letter-spacing: 2px; line-height: 1;
    color: var(--brand-green);
  }
  .card-back .wordmark {
    position: absolute; right: 40px; top: 108px;
    font-size: 60px;
  }
  /* logo side */
  .card-front { display: flex; align-items: center; justify-content: center; }
  .card-front .wordmark { font-size: 82px; }
</style>
</head>
<body>
  <main class="stage">
    <section class="card card-back" aria-label="Card back with contact details">
      <div class="holder">
        <p class="holder-name">Joanne <span class="surname">Lim</span></p>
        <p class="holder-role">Chief Operating Officer</p>
      </div>

      <p class="wordmark">NORVALE</p>

      <ul class="contact-list">
        <li>
          <svg viewBox="0 0 12 12" aria-hidden="true"><rect x="3" y="0.6" width="6" height="10.8" rx="1" fill="none" stroke="var(--brand-green)" stroke-width="1"/><line x1="5" y1="9.8" x2="7" y2="9.8" stroke="var(--brand-green)"/></svg>
          +65 9123 4567
        </li>
        <li>
          <svg viewBox="0 0 12 12" aria-hidden="true"><circle cx="6" cy="6" r="5.4" fill="var(--brand-blue)"/><ellipse cx="6" cy="6" rx="2.2" ry="5.4" fill="none" stroke="var(--card)" stroke-width=".8"/><line x1=".6" y1="6" x2="11.4" y2="6" stroke="var(--card)" stroke-width=".8"/></svg>
          www.norvalebrokers.com
        </li>
        <li>
          <svg viewBox="0 0 12 12" aria-hidden="true"><rect x=".6" y="2.4" width="10.8" height="7.4" fill="none" stroke="var(--brand-green)" stroke-width="1"/><polyline points=".8,2.8 6,7 11.2,2.8" fill="none" stroke="var(--brand-green)" stroke-width="1"/></svg>
          joanne@norvalebrokers.com
        </li>
      </ul>

      <p class="address">22 Harbour Lane, Meridian<br>Tower #08-04, Singapore 018942</p>
    </section>

    <section class="card card-front" aria-label="Card front">
      <p class="wordmark">NORVALE</p>
    </section>
  </main>
</body>
</html>
```